Brightmill Data Works

Our company is about IT hardwares and IT solutions. IT hardware such as PC, RAMS, storage and servers. IT solutions such as project management, BA. We are also selling new technology too.

Target Market(s)

Consumer, Small to Medium Business, Corporate

Requirements
Must have
• The business card must have the following:
• Name:
• Title:
• Contact Number:
• Email address:
• Website:
• Color: Must match the logo color upgrade

```html
<!DOCTYPE html>
<html lang="en">
<head>
<meta charset="utf-8">
<title>Brightmill Data Works – Business Card</title>
<link rel="stylesheet" href="https://fonts.googleapis.com/css2?family=Roboto:wght@400;700&display=swap">
<style>
  :root {
    --backdrop: #1d1d20;
    --card-dark: #3a3a3c;
    --card-light: #fbfbf9;
    --accent: #d98a2b;
    --ink: #2b2b2b;
    --ink-soft: #444446;
    --on-dark: #f3f3f3;
  }
  * { margin: 0; padding: 0; box-sizing: border-box; }
  html, body { width: 1200px; height: 800px; overflow: hidden; }
  body {
    background: var(--backdrop);
    font-family: "Roboto", Arial, sans-serif;
    position: relative;
  }
  .card {
    position: absolute;
    width: 560px;
    height: 320px;
  }
  .card-front {
    left: 70px;
    top: 70px;
    background: var(--card-dark);
    display: flex;
    align-items: center;
    justify-content: center;
  }
  .card-back {
    left: 570px;
    top: 410px;
    background: var(--card-light);
  }
  .brand {
    display: flex;
    align-items: center;
    gap: 12px;
    font-weight: 700;
    font-size: 26px;
    letter-spacing: 1px;
    text-transform: uppercase;
  }
  .brand-dot {
    width: 22px;
    height: 22px;
    border-radius: 50%;
    background: var(--accent);
    flex: none;
  }
  .card-front .brand { color: var(--on-dark); }
  .card-back .brand {
    position: absolute;
    right: 40px;
    top: 58px;
    font-size: 21px;
    color: var(--ink);
  }
  .divider {
    position: absolute;
    left: 36px;
    right: 36px;
    top: 188px;
    height: 2px;
    background: var(--accent);
  }
  .person {
    position: absolute;
    left: 40px;
    top: 140px;
  }
  .person-name {
    font-weight: 700;
    font-size: 19px;
    color: var(--ink-soft);
    text-transform: uppercase;
    line-height: 1.1;
  }
  .person-title {
    font-size: 16px;
    color: var(--accent);
    line-height: 1.2;
  }
  .contacts {
    position: absolute;
    left: 40px;
    top: 204px;
    list-style: none;
    font-size: 14px;
    color: var(--ink);
  }
  .contacts li {
    display: flex;
    align-items: center;
    gap: 8px;
    line-height: 24px;
  }
  .contacts svg { width: 12px; height: 12px; flex: none; }
  .address {
    position: absolute;
    right: 40px;
    top: 206px;
    font-size: 14px;
    line-height: 22px;
    color: var(--ink);
    font-style: normal;
    text-align: left;
  }
</style>
</head>
<body>
  <section class="card card-front" aria-label="Card front">
    <div class="brand"><span class="brand-dot"></span><span>Brightmill Data Works</span></div>
  </section>

  <section class="card card-back" aria-label="Card back">
    <div class="brand"><span class="brand-dot"></span><span>Brightmill Data Works</span></div>

    <div class="person">
      <p class="person-name">Mara Kellet</p>
      <p class="person-title">Manager</p>
    </div>

    <div class="divider"></div>

    <ul class="contacts">
      <li>
        <svg viewBox="0 0 12 12" aria-hidden="true"><path fill="#d98a2b" d="M2.5 1h2l1 2.6-1.3.9a6.5 6.5 0 0 0 3.3 3.3l.9-1.3 2.6 1v2c0 .8-.7 1.5-1.5 1.5A9.5 9.5 0 0 1 1 2.5C1 1.7 1.7 1 2.5 1z"/></svg>
        <span>555-201-4478</span>
      </li>
      <li>
        <svg viewBox="0 0 12 12" aria-hidden="true"><rect x="0.5" y="2" width="11" height="8" fill="#d98a2b"/><path d="M1 2.5 6 6.5l5-4" stroke="#fbfbf9" stroke-width="1" fill="none"/></svg>
        <span>info@brightmilldata.com</span>
      </li>
      <li>
        <svg viewBox="0 0 12 12" aria-hidden="true"><circle cx="6" cy="6" r="5.5" fill="#d98a2b"/><path d="M0.5 6h11M6 0.5c-2.5 3-2.5 8 0 11M6 0.5c2.5 3 2.5 8 0 11" stroke="#fbfbf9" stroke-width="0.8" fill="none"/></svg>
        <span>www.brightmilldata.com</span>
      </li>
    </ul>

    <address class="address">PO BOX 48 Harbor Lane<br>2nd street Ashford</address>
  </section>
</body>
</html>
```